Web Developer Wordpress theme

I'm a web developer but a poor designer so i need somebody to design me a cool and professional WordPress theme. I specialize in shopping cart developments and modifications as well as hosting for these system so would like the design to show this off. I am UK based and want this to also come across in the design.
As for colors and layout i am open mined just use your imaginantion i will let know what i think of your designs.
also forgot to mention my business name is valtrique
and my exsiting site is valtrique.co.uk

```html
<!DOCTYPE html>
<html lang="en">
<head>
<meta charset="utf-8">
<title>Valtrique – serious web development</title>
<link href="https://fonts.googleapis.com/css2?family=Roboto+Condensed:wght@400;700&family=Roboto:wght@400;500&display=swap" rel="stylesheet">
<style>
:root{
  --bg-dark:#3e3e3e;
  --panel:#5a5a5a;
  --panel-dark:#4a4a4a;
  --orange:#f0902a;
  --orange-deep:#e27a12;
  --text-light:#e4e4e4;
  --link-blue:#3a9fd8;
  --btn-blue-dark:#145384;
  --footer-bg:#e4e4e4;
  --footer-text:#5f5f5f;
  --bottom-bar:#fafafa;
  --logo-bg:#d9d9d9;
}
*{box-sizing:border-box;margin:0;padding:0}
html,body{width:1200px;height:1080px;overflow:hidden;background:#fff}
body{font-family:"Roboto",Arial,sans-serif}
.canvas{position:relative;width:1200px;height:1080px;overflow:hidden}
.masthead{position:absolute;left:0;top:0;width:1200px;height:802px;
  background:var(--bg-dark);
  background-image:repeating-linear-gradient(45deg,rgba(255,255,255,.025) 0 2px,transparent 2px 4px),repeating-linear-gradient(-45deg,rgba(0,0,0,.06) 0 2px,transparent 2px 4px)}
.abs{position:absolute}
.logo-box{left:72px;top:0;width:319px;height:110px;background:var(--logo-bg);border-radius:0 0 8px 8px;box-shadow:0 6px 8px rgba(0,0,0,.35);display:flex;flex-direction:column;align-items:center;justify-content:center;gap:2px}
.logo-name{font-family:"Roboto Condensed",Arial,sans-serif;font-weight:700;font-size:50px;color:var(--orange);line-height:1;display:flex;align-items:center;gap:10px}
.logo-name i{display:block;width:16px;height:16px;border-radius:50%;background:var(--orange)}
.logo-tag{font-family:"Roboto Condensed",Arial,sans-serif;font-size:13px;color:#555;letter-spacing:2px;border-top:1px solid #999;padding-top:2px}
.social{left:972px;top:0;width:157px;height:53px;background:#555;border-radius:0 0 8px 8px;display:flex;align-items:center;justify-content:center;gap:16px}
.social span{width:36px;height:36px;border-radius:50%;background:#8a8a8a}
.social span.first{background:var(--orange)}
.nav{left:486px;top:65px;width:643px;height:48px;background:#585858;border-radius:7px;display:flex;align-items:center;justify-content:flex-end;padding-right:38px;gap:42px;font-family:"Roboto Condensed",Arial,sans-serif;font-size:21px;color:#fff}
.post-thumb{left:72px;width:156px;height:156px;border:4px solid #fff;border-radius:14px;background:linear-gradient(160deg,#cfe0f5 0%,#4d86d6 55%,#1f4fa0 100%)}
.post-title{left:249px;width:440px;font-family:"Roboto Condensed",Arial,sans-serif;font-weight:400;font-size:26px;line-height:31px;color:var(--orange)}
.post-body{left:251px;width:552px;font-size:13px;line-height:23px;color:var(--text-light)}
.post-meta{left:247px;width:556px;height:33px;background:#575757;padding-left:12px;font-size:13px;line-height:33px;color:var(--text-light)}
.post-meta a{color:var(--link-blue);text-decoration:none}
.btn{height:28px;border-radius:14px;background:linear-gradient(#3b8fd0,var(--btn-blue-dark));color:#fff;font-size:12px;display:flex;align-items:center;justify-content:space-between;padding:0 6px 0 14px;box-shadow:0 2px 3px rgba(0,0,0,.4)}
.btn svg{width:18px;height:18px}
.divider{left:72px;width:732px;height:2px;background:#1e1e1e;border-bottom:1px solid #555}
.sidebar{left:833px;top:143px;width:296px;height:637px;background:var(--panel);border-radius:8px;box-shadow:0 3px 8px rgba(0,0,0,.4)}
.search{left:844px;top:156px;width:273px;height:34px;background:var(--panel-dark);border-radius:8px;color:#fff;font-size:13px;line-height:34px;padding-left:14px}
.search svg{position:absolute;right:10px;top:6px}
.ad{width:128px;height:122px;border:5px solid #444;background:linear-gradient(160deg,#1a1a1a,#000)}
.side-head{left:843px;width:275px;font-family:"Roboto Condensed",Arial,sans-serif;font-weight:700;font-size:26px;color:#fff;border-bottom:1px solid #7a7a7a;padding-bottom:4px}
.side-links{left:844px;top:505px;width:275px;list-style:none;font-size:15px;color:#eee}
.side-links li{height:26px;line-height:26px;padding-left:24px;position:relative}
.side-links li::before{content:"";position:absolute;left:8px;top:9px;width:7px;height:7px;border-top:2px solid var(--orange);border-right:2px solid var(--orange);transform:rotate(45deg)}
.side-links li.active{background:linear-gradient(90deg,var(--orange-deep) 0%,var(--orange) 60%,transparent 100%)}
.side-links li.active::before{border-color:#fff}
.email{left:844px;top:685px;width:275px;height:35px;background:var(--panel-dark);border-radius:8px;color:#fff;font-size:13px;line-height:35px;padding-left:15px}
.footer{left:0;top:802px;width:1200px;height:242px;background:var(--footer-bg)}
.foot-head{font-family:"Roboto Condensed",Arial,sans-serif;font-weight:400;font-size:26px;color:#555;border-bottom:1px solid #ccc;width:266px;padding-bottom:4px}
.foot-blog{left:104px;width:266px;font-size:13px;line-height:24px;color:var(--footer-text);border-bottom:1px solid #d0d0d0;padding-bottom:4px}
.foot-blog a{color:var(--link-blue);text-decoration:none;display:block}
.field{left:467px;width:265px;background:#fff;border:1px solid #d8d8d8;font-size:13px;color:#666;padding:8px 0 0 9px}
.promo{left:842px;top:868px;width:248px;height:138px;background:linear-gradient(#3ea8e6,#1d78c0);border-radius:4px;box-shadow:0 6px 6px rgba(0,0,0,.25);color:#fff;padding:30px 0 0 64px;overflow:hidden}
.promo h3{font-family:"Roboto Condensed",Arial,sans-serif;font-weight:400;font-size:19px;line-height:22px;white-space:nowrap}
.promo p{font-size:12px;line-height:17px;margin-top:4px}
.promo a{font-size:11px;color:#fff;display:inline-block;margin-top:6px;text-decoration:underline}
.ribbon{left:828px;top:892px;width:104px;height:22px;background:#c21d24;color:#fff;font-size:10px;text-align:center;line-height:22px;transform:rotate(-45deg)}
.pager{top:1014px;width:16px;height:16px;border-radius:50%;background:#888}
.bottom{left:0;top:1044px;width:1200px;height:36px;background:var(--bottom-bar);text-align:center;font-size:13px;line-height:36px;color:#aaa}
</style>
</head>
<body>
<div class="canvas">
  <div class="masthead"></div>

  <div class="abs logo-box">
    <div class="logo-name"><i></i>Valtrique</div>
    <div class="logo-tag">serious web development</div>
  </div>

  <div class="abs social"><span class="first"></span><span></span><span></span></div>

  <nav class="abs nav"><span>Home</span><span>About Us</span><span>Services</span><span>Addons</span><span>Contact</span><span>Blog</span></nav>

  <div class="abs post-thumb" style="top:154px" role="img" aria-label="Blog illustration with cursor"></div>
  <h2 class="abs post-title" style="top:148px">Lorem ipsum dolor sit amet, consectetur adipiscing elit. Mauris ut</h2>
  <p class="abs post-body" style="top:218px">Lorem Ipsum is simply dummy text of the printing and typesetting industry. Lorem Ipsum has been the industry's standard dummy text ever since the 1500s, when an unknown printer took a galley of type and scrambled it to make a type specimen book. It has survived not only five centuries, but also the leap into electronic typesetting, remaining essentially unchanged.</p>
  <div class="abs post-meta" style="top:320px">Posted by <a>Valtrique</a> on Jan 3, 2012 | <a>0 comments</a></div>
  <div class="abs btn" style="left:253px;top:367px;width:101px">Read more<svg viewBox="0 0 18 18"><circle cx="9" cy="9" r="8" fill="#fff"/><path d="M7 5l4 4-4 4" stroke="#145384" stroke-width="2.4" fill="none"/></svg></div>
  <div class="abs divider" style="top:406px"></div>

  <div class="abs post-thumb" style="top:436px" role="img" aria-label="Blog illustration with cursor"></div>
  <h2 class="abs post-title" style="top:430px">Lorem ipsum dolor sit amet, consectetur adipiscing elit. Mauris ut</h2>
  <p class="abs post-body" style="top:500px">Lorem Ipsum is simply dummy text of the printing and typesetting industry. Lorem Ipsum has been the industry's standard dummy text ever since the 1500s, when an unknown printer took a galley of type and scrambled it to make a type specimen book. It has survived not only five centuries, but also the leap into electronic typesetting, remaining essentially unchanged.</p>
  <div class="abs post-meta" style="top:602px">Posted by <a>Valtrique</a> on Jan 3, 2012 | <a>0 comments</a></div>
  <div class="abs btn" style="left:253px;top:649px;width:101px">Read more<svg viewBox="0 0 18 18"><circle cx="9" cy="9" r="8" fill="#fff"/><path d="M7 5l4 4-4 4" stroke="#145384" stroke-width="2.4" fill="none"/></svg></div>
  <div class="abs divider" style="top:688px"></div>

  <aside class="abs sidebar"></aside>
  <div class="abs search">Search here....<svg width="24" height="24" viewBox="0 0 24 24"><circle cx="9" cy="9" r="6" stroke="#fff" stroke-width="2.5" fill="none"/><path d="M13.5 13.5l8 7" stroke="#fff" stroke-width="3.5" stroke-linecap="round"/></svg></div>

  <div class="abs ad" style="left:845px;top:202px" role="img" aria-label="Advertising banner"></div>
  <div class="abs ad" style="left:989px;top:202px" role="img" aria-label="Advertising banner"></div>
  <div class="abs ad" style="left:845px;top:334px" role="img" aria-label="Advertising banner"></div>
  <div class="abs ad" style="left:989px;top:334px" role="img" aria-label="Advertising banner"></div>

  <h3 class="abs side-head" style="top:462px">Links Here</h3>
  <ul class="abs side-links">
    <li class="active">Home</li><li>About Us</li><li>Services</li><li>Addons</li><li>Contact Us</li>
  </ul>
  <h3 class="abs side-head" style="top:638px">Subscribe</h3>
  <div class="abs email">Enter email</div>
  <div class="abs btn" style="left:848px;top:734px;width:101px">Subscribe<svg viewBox="0 0 18 18"><circle cx="9" cy="9" r="8" fill="#fff"/><path d="M7 5l4 4-4 4" stroke="#145384" stroke-width="2.4" fill="none"/></svg></div>

  <div class="abs footer"></div>
  <h3 class="abs foot-head" style="left:102px;top:812px">From Blog</h3>
  <div class="abs foot-blog" style="top:856px"><a>Quisque euismod orci...</a>Nulla luctus, purus in molestie posuere, lorem...</div>
  <div class="abs foot-blog" style="top:940px"><a>Quisque euismod orci...</a>Nulla luctus, purus in molestie posuere, lorem...</div>

  <h3 class="abs foot-head" style="left:467px;top:812px">Quick Contact</h3>
  <div class="abs field" style="top:859px;height:30px">Name</div>
  <div class="abs field" style="top:894px;height:30px">Email</div>
  <div class="abs field" style="top:929px;height:71px">Subject</div>
  <div class="abs btn" style="left:470px;top:1007px;width:102px">SUBMIT<svg viewBox="0 0 18 18"><circle cx="9" cy="9" r="8" fill="#fff"/><path d="M7 5l4 4-4 4" stroke="#145384" stroke-width="2.4" fill="none"/></svg></div>

  <h3 class="abs foot-head" style="left:832px;top:812px">Quickstart Package</h3>
  <div class="abs promo">
    <h3>Shopping Cart Hosting</h3>
    <p>Lorem ipsum dolor sit amet, consectetuer adipiscing elit,</p>
    <a>Learn more</a>
  </div>
  <div class="abs ribbon">ORDER NOW</div>
  <div class="abs pager" style="left:1043px"></div>
  <div class="abs pager" style="left:1067px"></div>

  <div class="abs bottom">Website content Copyrighted Valtrique 2012</div>
</div>
</body>
</html>
```